Hardcore nerd needs to stand out in a sea of dull Defence business cards

Wombarra Devices is a new Australian consulting engineering company that turns research and theory into practical systems. No evangelistic fluff, just mathematics and physics into electronic and optical circuits for consumer products, scientific research or Defence applications.

We already have a recognised logo (provided) which is often dark blue/black on a light background but we're open to other combinations. (Us engineers tend to have limited aesthetic imagination :)

Some of our recent products have included:
* Instrumentation for electrical testing,
* Radar jammers,
* GPS antenna design,
* Satellite tracking systems,
* High power lasers

We're open to both single and double-sided designs - happy to be convinced either way.

P.S. Another group is working on the web page, so - alas - our web site is currently of no use for images/ideas...

Target Market(s)

Engineering managers,
Scientists

Contact Information for Business Card

Dr Colin Harte
R&D Engineer

colin@wombarradevices.com.au
0427 563 710

PO Box XXX (to be confirmed)
Kelsby ACT 2917
Australia

Font styles to use
Serif
Sans Serif

Colors

Designer to choose colors to be used in the design.

Requirements
Must have
• My contact details!
• I've had many (great) "bold and plain" designs submitted already, so feel free to be artistically creative :)
• Happy to take advice re fonts/colours/printability etc.
Nice to have
• I'm not sure if "lists" are more at home on a CV than a business card, but representative services include:
• Applied electromagnetics
• RF and high speed electronics
• Signal and image processing
• Electro-optical and laser systems
• Concept-to-prototype design services
• If you're considering double sided cards, then often measuring/alignment grids/rulers feature on the back of similar cards.
• e.g. https://www.veltranoptics.example/newgrouppage9.cfm?objectgroup_id=4183
• https://www.veltranoptics.example/newgrouppage9.cfm?objectgroup_ID=4185
• ..or even a "Smith chart" (google will return lots)
• Generic images to represent a capability might work - googling images associated with keyword for each of these areas might help:
• - "passive radar", "phased array", "fdtd", "vircator"
• RF and high speed electronic design
• - "smith chart", "microstrip circuits", "dimensioned drawing", "electronic schematic"
• - "dft", "iir filter"
• - "optical cavity". "laser energy level diagram"
• Background/watermarked images outlines/wireframes/schematics would probably look OK.
Should not have
• If a list of projects/services is provided, it is important not to make the client feel that this is "all" the company can do. Engineering design is a creative discipline (like graphics :)
• Please, no stock "military" snaps like planes, missiles, etc!

```html
<!DOCTYPE html>
<html lang="en">
<head>
<meta charset="utf-8">
<title>Wombarra Devices – Business Card</title>
<link rel="stylesheet" href="https://fonts.googleapis.com/css2?family=Arimo:wght@700&family=Lato:wght@400;700&display=swap">
<style>
  :root {
    --navy: #0b1f5c;
    --white: #ffffff;
    --ink: #1f2230;
    --backdrop: #d9d9d9;
  }
  * { margin: 0; padding: 0; box-sizing: border-box; }
  html, body {
    width: 1200px;
    height: 802px;
    overflow: hidden;
    background: var(--backdrop);
  }
  .stage { position: relative; width: 1200px; height: 802px; }
  .card {
    position: absolute;
    top: 274px;
    width: 443px;
    height: 264px;
    overflow: hidden;
  }
  .card--front { left: 136px; background: var(--white); }
  .card--back { left: 624px; background: var(--navy); }

  .front-shape { position: absolute; inset: 0; }

  .holder { position: absolute; left: 20px; top: 41px; }
  .holder__name {
    font-family: "Arimo", Arial, sans-serif;
    font-weight: 700;
    font-size: 16px;
    line-height: 16px;
    color: var(--navy);
  }
  .holder__role {
    font-family: "Lato", sans-serif;
    font-size: 12.5px;
    line-height: 14px;
    color: var(--ink);
  }

  .address {
    position: absolute;
    left: 20px;
    top: 115px;
    font-family: "Lato", sans-serif;
    font-size: 12.5px;
    line-height: 16px;
    color: var(--ink);
  }

  .contact {
    position: absolute;
    left: 20px;
    top: 164px;
    list-style: none;
    font-family: "Lato", sans-serif;
    font-size: 12.5px;
    line-height: 16px;
    color: var(--ink);
  }
  .contact__item { display: flex; align-items: center; gap: 5px; }
  .contact__icon { width: 10px; height: 10px; fill: var(--navy); flex: none; }

  .brand {
    position: absolute;
    left: 0; right: 0; top: 0; bottom: 0;
    display: flex;
    align-items: center;
    justify-content: center;
    gap: 12px;
  }
  .brand__dot {
    width: 44px; height: 44px;
    border-radius: 50%;
    background: var(--white);
  }
  .brand__name {
    font-family: "Lato", sans-serif;
    font-weight: 700;
    color: var(--white);
    letter-spacing: 1.5px;
    text-transform: uppercase;
    line-height: 1.1;
  }
  .brand__line--main { font-size: 26px; display: block; }
  .brand__line--sub { font-size: 15px; display: block; letter-spacing: 4px; }
</style>
</head>
<body>
<main class="stage">

  <section class="card card--front" aria-label="Business card front">
    <svg class="front-shape" width="443" height="264" viewBox="0 0 443 264" aria-hidden="true">
      <circle cx="449" cy="115" r="118" fill="var(--navy)"/>
      <path d="M365 190 Q380 230 386 226 L443 226 L443 200 Z" fill="var(--navy)"/>
      <path d="M0 226 L360 226 Q380 226 386 228 Q370 220 365 210 L443 210 L443 264 L0 264 Z" fill="var(--navy)"/>
    </svg>

    <div class="holder">
      <p class="holder__name">DR COLIN HARTE</p>
      <p class="holder__role">R&amp;D Engineer</p>
    </div>

    <address class="address" style="font-style:normal">
      PO Box XXX<br>
      Kelsby ACT 2917, Australia
    </address>

    <ul class="contact">
      <li class="contact__item">
        <svg class="contact__icon" viewBox="0 0 10 10" aria-hidden="true"><path d="M1 2.5 Q1 1 3 1 L7 1 Q9 1 9 2.5 L9 3.5 L7 3.5 L7 2.5 L3 2.5 L3 3.5 L1 3.5 Z M2.5 4.5 L7.5 4.5 L9 9 L1 9 Z"/></svg>
        0427 563 710
      </li>
      <li class="contact__item">
        <svg class="contact__icon" viewBox="0 0 10 10" aria-hidden="true"><path d="M0.5 2 L9.5 2 L9.5 8.5 L0.5 8.5 Z M1.2 2.6 L5 5.6 L8.8 2.6" stroke="#fff" stroke-width="0.8"/></svg>
        colin@wombarradevices.com.au
      </li>
      <li class="contact__item">
        <svg class="contact__icon" viewBox="0 0 10 10" aria-hidden="true"><circle cx="5" cy="5" r="4.5"/><path d="M0.5 5 H9.5 M5 0.5 Q2.5 5 5 9.5 M5 0.5 Q7.5 5 5 9.5" stroke="#fff" stroke-width="0.7" fill="none"/></svg>
        www.wombarradevices.com.au
      </li>
    </ul>
  </section>

  <section class="card card--back" aria-label="Business card back">
    <div class="brand">
      <span class="brand__dot" aria-hidden="true"></span>
      <p class="brand__name">
        <span class="brand__line--main">Wombarra</span>
        <span class="brand__line--sub">Devices</span>
      </p>
    </div>
  </section>

</main>
</body>
</html>
```